A business card design for a dental office. We have Two doctors working here. We practice general de

I already have a logo designed for the office with the name and a slogan.
Now I need to create design for a business card using the same logo.
Details Needed on the front side of the card are :
Bernard K. Oswin, DDS
Gerald M Fenwick, DDS
418 Birch Lane
Ashgrove, NH 00000
Phone : 555 019 4831
Fax : 555 019 4832
Website : WWW.BrightmoorToothHaven.Com
Office hours by appointment
On the back side of the card need :
Appointment
Date....................Time...................
With....................................
If unable to keep your appointment, please give 24-48 hours notice in order to avoid broken appointment fee.

Industry/Entity Type

Dental Clinic

Contact Information for Business Card

Bernard K. Oswin, DDS
Gerald M Fenwick, DDS
418 Birch Lane
Ashgrove, NH 00000
Phone : 555 019 4831
Fax : 555 019 4832
Appointment

Requirements
Must have
• Keep the Name and slogan on the logo on the front of the card. You can move them around the Logo and Name/Slogan of business (Oswin Family Dentistry/We give you reasons to smile) as you wish to get a feel of the design.
• Bernard K. Oswin, DDS
• Gerald M Fenwick, DDS
• 418 Birch Lane
• Ashgrove, NH 00000
• Phone : 555 019 4831
• Fax : 555 019 4832
• WWW.BrightmoorToothHaven.Com
• Keep these three groups above as they are together now in different areas of the front side.
• On the back side of the card need :
• Appointment
• Date....................Time...................
• With....................................
• If unable to keep your appointment, please give 24-48 hours notice in order to avoid broken appointment fee.

```html
<!DOCTYPE html>
<html lang="en">
<head>
<meta charset="utf-8">
<title>Oswin Family Dentistry – Business Card</title>
<link href="https://fonts.googleapis.com/css2?family=Source+Sans+3:ital,wght@0,400;0,600;1,400;1,600&display=swap" rel="stylesheet">
<style>
  :root {
    --bg: #a4a4a4;
    --card: #f7f7f8;
    --blue: #1a5aa6;
    --navy: #1d4f8f;
    --red: #e02b33;
    --teal-rule: #5f9e98;
    --ink: #4a4a4a;
    --muted: #5c5c5c;
  }
  * { box-sizing: border-box; margin: 0; padding: 0; }
  html, body { width: 1105px; height: 1200px; overflow: hidden; }
  body {
    background: var(--bg);
    font-family: "Source Sans 3", "Myriad Pro", sans-serif;
    position: relative;
  }
  .card {
    position: absolute;
    left: 181px;
    width: 747px;
    background: var(--card);
    overflow: hidden;
  }
  .card--front { top: 119px; height: 424px; }
  .card--back { top: 635px; height: 426px; }

  /* front */
  .brand {
    position: absolute;
    left: 417px; top: 31px; width: 312px;
    text-align: center;
  }
  .brand__mark {
    width: 106px; height: 106px; border-radius: 50%;
    background: var(--blue);
    margin: 0 auto 10px;
  }
  .brand__name {
    font-size: 21px; font-weight: 600; letter-spacing: 1.2px;
    color: var(--navy); text-transform: uppercase; white-space: nowrap;
  }
  .doctors {
    position: absolute; left: 33px; top: 222px;
    color: var(--blue); font-size: 27px; font-weight: 600; line-height: 31px;
  }
  .doctors .title { font-size: 19px; font-weight: 400; }
  .rule {
    position: absolute; left: 33px; top: 293px; width: 682px; height: 2px;
    background: var(--teal-rule);
  }
  .contacts {
    position: absolute; left: 33px; top: 304px; list-style: none;
    color: var(--ink); font-size: 19px; line-height: 29px;
  }
  .contacts li { display: flex; align-items: center; gap: 8px; }
  .contacts svg { width: 18px; height: 18px; fill: var(--navy); }
  .location {
    position: absolute; right: 33px; top: 333px; text-align: right;
    font-size: 19px; line-height: 29px;
  }
  .location__address { color: var(--ink); }
  .location__hours { color: var(--blue); font-style: italic; font-weight: 600; }
  .stripe { position: absolute; left: 0; bottom: 0; width: 747px; height: 12px; }

  /* back */
  .appointment__title {
    position: absolute; top: 38px; left: 0; width: 100%; text-align: center;
    color: var(--blue); font-size: 28px; font-weight: 600;
  }
  .dots {
    position: absolute; border-bottom: 2px dotted #8a8a8a; height: 0;
  }
  .label { position: absolute; font-size: 20px; }
  .label--ink { color: var(--ink); }
  .label--blue { color: var(--blue); }
  .label--small { font-size: 16px; }
  .days {
    position: absolute; top: 276px; left: 0; width: 100%; list-style: none;
  }
  .days li {
    position: absolute; display: flex; align-items: center; gap: 6px;
    color: var(--blue); font-size: 20px;
  }
  .days .box {
    width: 20px; height: 18px; border: 1.5px solid #555; background: #fff;
  }
  .notice {
    position: absolute; top: 354px; left: 0; width: 100%; text-align: center;
    color: var(--muted); font-size: 16px; font-style: italic; line-height: 22px;
  }
</style>
</head>
<body>

<section class="card card--front" aria-label="Business card front">
  <div class="brand">
    <div class="brand__mark"></div>
    <div class="brand__name">Oswin Family Dentistry</div>
  </div>

  <div class="doctors">
    <div>Bernard K. Oswin, <span class="title">DDS</span></div>
    <div>Gerald M Fenwick, <span class="title">DDS</span></div>
  </div>

  <div class="rule"></div>

  <ul class="contacts">
    <li>
      <svg viewBox="0 0 24 24" aria-hidden="true"><path d="M6.6 10.8a15.1 15.1 0 0 0 6.6 6.6l2.2-2.2c.3-.3.7-.4 1-.2 1.1.4 2.3.6 3.6.6.6 0 1 .4 1 1V20c0 .6-.4 1-1 1A17 17 0 0 1 3 4c0-.6.4-1 1-1h3.5c.6 0 1 .4 1 1 0 1.3.2 2.5.6 3.6.1.3 0 .7-.2 1z"/></svg>
      555 019 4831
    </li>
    <li>
      <svg viewBox="0 0 24 24" aria-hidden="true"><path d="M6 2h10l2 2v5H6zM3 10h18a2 2 0 0 1 2 2v6h-4v4H5v-4H1v-6a2 2 0 0 1 2-2zm4 7v3h10v-3z"/></svg>
      555 019 4832
    </li>
    <li>
      <svg viewBox="0 0 24 24" aria-hidden="true"><path d="M12 2a10 10 0 1 0 0 20 10 10 0 0 0 0-20zm-1 17.9A8 8 0 0 1 4.2 10L9 15v1a2 2 0 0 0 2 2zm6.9-2.5A2 2 0 0 0 16 16h-1v-3a1 1 0 0 0-1-1H8v-2h2a1 1 0 0 0 1-1V7h2a2 2 0 0 0 2-2v-.4a8 8 0 0 1 2.9 12.8z"/></svg>
      BrightmoorToothHaven.Com
    </li>
  </ul>

  <div class="location">
    <div class="location__address">418 Birch Lane, Ashgrove, NH 00000</div>
    <div class="location__hours">Office hours by appointment</div>
  </div>

  <svg class="stripe" viewBox="0 0 747 12" preserveAspectRatio="none" aria-hidden="true">
    <polygon points="0,0 487,0 483,12 0,12" fill="var(--blue)"/>
    <polygon points="493,0 747,0 747,12 489,12" fill="var(--red)"/>
  </svg>
</section>

<section class="card card--back" aria-label="Business card back">
  <h1 class="appointment__title">Next Appointment</h1>

  <div class="dots" style="left:45px; top:134px; width:433px;"></div>
  <span class="label label--ink" style="left:489px; top:113px;">has an appointment</span>

  <span class="label label--blue" style="left:36px; top:190px;">Date :</span>
  <div class="dots" style="left:109px; top:211px; width:280px;"></div>
  <span class="label label--blue" style="left:414px; top:190px;">Time :</span>
  <div class="dots" style="left:478px; top:211px; width:146px;"></div>
  <span class="label label--blue label--small" style="left:630px; top:195px;">AM/PM</span>

  <ul class="days">
    <li style="left:43px;">Sun <span class="box"></span></li>
    <li style="left:137px;">Mon <span class="box"></span></li>
    <li style="left:238px;">Tue <span class="box"></span></li>
    <li style="left:344px;">Wed <span class="box"></span></li>
    <li style="left:446px;">Thu<span class="box"></span></li>
    <li style="left:548px;">Fri <span class="box"></span></li>
    <li style="left:628px;">Sat <span class="box"></span></li>
  </ul>

  <p class="notice">Please give me 24 hours notice if you are unable to keep your appointment or<br>a cancellation fee may be charged.</p>
</section>

</body>
</html>
```